Keystone Polished Concrete & Grinding
I'm looking for a business card and logo design for my
new Polished Concrete & Grinding business,
If you were to look up Keystone in the dictionary it would
say, first in importance, order, or position; leading.
Polished Concrete floors are a niche market, that are being used currently in Shopping centres, office spaces and by most high end architects, builders and designers.
i need my business card & logo to stand out from my
competitors, i need my design + logo to reflect this it
needs to be simple, professional, eye catching, easy
to read and scream quality. The logo will need to be
suitable for a whole range of applications including,
uniforms, letter heads, stickers, and eventually
incorporating in vehicle vinyl wrapping.
Target Market(s)
Builders, architects, Interior designers & home owners
Contact Information for Business Card
Front side:
- Keystone Polished Concrete & Grinding.
- Logo
Rear side:
- Liam Varesko
- 0438175092
- info@keystonepcg-example.com.au
- commercial - domestic - industrial
- (later down the line website & space for
social media links
www.keystonepolishedslab-example.com.au)
Colors
Designer to choose colors to be used in the design.
Look and feel
Each slider illustrates characteristics of the customer's brand and the style your logo design should communicate.

```html
<!DOCTYPE html>
<html lang="en">
<head>
<meta charset="utf-8">
<title>Keystone Polished Concrete &amp; Grinding – Business Card</title>
<link rel="stylesheet" href="https://fonts.googleapis.com/css2?family=Roboto:wght@400;500&display=swap">
<style>
  :root {
    --stage: #3a3a3c;
    --card-dark: #1c1b1d;
    --card-white: #ffffff;
    --card-grey: #e6e7e9;
    --brand-blue: #1fa3de;
    --brand-blue-deep: #1580bf;
    --text-light: #f2f2f2;
  }
  * { box-sizing: border-box; margin: 0; padding: 0; }
  html, body { width: 1200px; height: 900px; overflow: hidden; }
  body {
    background: var(--stage);
    font-family: "Roboto", Arial, sans-serif;
    position: relative;
  }
  .card {
    position: absolute;
    left: 280px;
    width: 640px;
    height: 366px;
    border-radius: 22px;
    overflow: hidden;
    box-shadow: 0 12px 30px rgba(0,0,0,0.45);
  }
  .card--front { top: 52px; background: var(--card-white); }
  .card--back { top: 474px; background: var(--card-dark); }
  .card__wave { position: absolute; inset: 0; width: 100%; height: 100%; }

  .brand {
    position: absolute;
    display: flex;
    align-items: center;
    gap: 14px;
    font-weight: 500;
    color: var(--brand-blue);
    text-transform: uppercase;
    line-height: 1.15;
  }
  .brand__dot {
    width: 22px; height: 22px;
    border-radius: 50%;
    background: var(--brand-blue);
    flex: none;
  }
  .card--front .brand { left: 56px; top: 58px; font-size: 24px; width: 330px; }
  .card--back .brand { left: 150px; top: 110px; font-size: 28px; width: 400px; }

  .holder {
    position: absolute;
    right: 40px;
    top: 220px;
    text-align: right;
  }
  .holder__name {
    color: var(--brand-blue);
    font-size: 30px;
    font-weight: 400;
    letter-spacing: 1.5px;
    text-transform: uppercase;
  }
  .holder__role {
    color: var(--text-light);
    font-size: 15px;
    margin-top: 2px;
  }
  .contacts {
    list-style: none;
    margin-top: 12px;
  }
  .contacts li {
    display: flex;
    justify-content: flex-end;
    align-items: center;
    gap: 8px;
    color: var(--text-light);
    font-size: 15px;
    line-height: 22px;
  }
  .contacts svg { width: 12px; height: 12px; flex: none; }

  .services {
    position: absolute;
    left: 0; right: 0;
    top: 262px;
    text-align: center;
    color: var(--text-light);
    font-size: 20px;
    letter-spacing: 1px;
    text-transform: uppercase;
  }
</style>
</head>
<body>

<section class="card card--front" aria-label="Business card contact side">
  <svg class="card__wave" viewBox="0 0 640 366" preserveAspectRatio="none" aria-hidden="true">
    <defs>
      <linearGradient id="paperShade" x1="0" y1="0" x2="1" y2="1">
        <stop offset="0" stop-color="#ffffff"/>
        <stop offset="1" stop-color="#e3e4e6"/>
      </linearGradient>
    </defs>
    <rect width="640" height="366" fill="url(#paperShade)"/>
    <path d="M0,120 C40,170 120,200 240,196 C380,192 520,180 640,150 L640,170 C520,196 380,206 240,210 C120,214 40,190 0,150 Z" fill="var(--brand-blue)"/>
    <path d="M0,158 C40,198 120,222 240,220 C380,218 520,206 640,178 L640,366 L0,366 Z" fill="var(--card-dark)"/>
  </svg>

  <div class="brand"><span class="brand__dot"></span><span>Keystone Polished Concrete &amp; Grinding</span></div>

  <div class="holder">
    <h1 class="holder__name">Liam Varesko</h1>
    <p class="holder__role">Director</p>
    <ul class="contacts">
      <li>0438175092
        <svg viewBox="0 0 12 12"><path d="M3 1 L5 3.5 L4 5 C4.8 6.6 5.6 7.4 7 8 L8.5 7 L11 9 L9.5 11 C5 10.5 1.5 7 1 2.5 Z" fill="var(--brand-blue)"/></svg>
      </li>
      <li>info@keystonepcg-example.com.au
        <svg viewBox="0 0 12 12"><rect x="1" y="2.5" width="10" height="7" rx="1" fill="none" stroke="var(--brand-blue)" stroke-width="1.3"/><path d="M1.5 3 L6 6.5 L10.5 3" fill="none" stroke="var(--brand-blue)" stroke-width="1.3"/></svg>
      </li>
      <li>www.keystonepolishedslab-example.com.au
        <svg viewBox="0 0 12 12"><circle cx="6" cy="6" r="5" fill="none" stroke="var(--brand-blue)" stroke-width="1.2"/><ellipse cx="6" cy="6" rx="2.2" ry="5" fill="none" stroke="var(--brand-blue)" stroke-width="1"/><path d="M1 6 H11" stroke="var(--brand-blue)" stroke-width="1"/></svg>
      </li>
    </ul>
  </div>
</section>

<section class="card card--back" aria-label="Business card brand side">
  <div class="brand"><span class="brand__dot"></span><span>Keystone Polished Concrete &amp; Grinding</span></div>
  <p class="services">Commercial - Domestic - Industrial</p>
</section>

</body>
</html>
```